Solvara - Arch Comfort Co. Seeks Improved Product Packaging

Our initial product was launched and we now have a version that is interchangeable per customer demand. Our existing package is too costly to mail. The Coastal mail carrier says we could mail them for regular postage if it was flexible and thin.

So this is our chance to improve the product and make the packaging have a WOW factor.

Our competitor's packages are really boring, so we want to spice things up - afte rall this product solves high heel hell!

*New Product Name: Living in High Heel Hell? Then try the only High Heel Insert with a Metatarsal Depression that Relieves Ball of Foot Pain!

We are no absolutely loving the hell and Heaven idea. We are open to more ideas for packing. Maybe a retro look, black and white with a pop of color. We want an elegant way to portray that we relieve pain and the results are amazing!

Target Market(s)

Women 25 - 55

Industry/Entity Type

Product

Font styles to use
Other font styles liked:
• Fertigo Pro Regular

Requirements
Must have
• *Flexible foil package 4 inch by 8 inch by 1/2 inch
• * Barcode
• *Made in China
• * Text box of what it includes ( 1 pair)
• *Logo should stay the same (ok to vary colors in it) Solvara is trademarked
• *Editable product name/description
• *Editable Story section
• *Editable Tag line (addressing pain we solve or reason to buy)
• *Editable Tag line on how we solve it
• *One insert is showing thru package (other is hidden)
• *Retail hole punch for hanging
• * inserts must be separated with a seal to keep them from sliding on top of each other - this is to keep it as thin as possible. The inserts are each 3;.5mm thick
• * Direction for placement editable section
Nice to have
• We are reopening the project as the owners are not all loving the Heaven and Hell theme. This is designed for women and is considered a luxury item but meeting a huge need of eliminating pain when were heels and loving wearing them again. Any design that will set that off. We are open
Should not have
• Be to busy....should flow and sell it.
• Colors should flow and match.

```html
<!DOCTYPE html>
<html lang="en">
<head>
<meta charset="utf-8">
<title>Solvara – Insert Package</title>
<link rel="stylesheet" href="https://fonts.googleapis.com/css2?family=Cinzel:wght@400;600&family=Marcellus&family=Tenor+Sans&family=Exo+2:ital,wght@1,700&family=Arimo:ital@0;1&display=swap">
<style>
  :root {
    --backdrop-top: #f4f4f4;
    --backdrop-bottom: #9d9d9d;
    --hell-black: #0b0606;
    --hell-brown: #5a2412;
    --flame-deep: #b8300e;
    --flame: #f07a1a;
    --flame-light: #ffcf4a;
    --gold: #f1d68a;
    --white: #ffffff;
    --cloud-blue: #bfe6f5;
    --cloud-light: #eaf8fd;
    --tagline-blue: #0d4f8c;
    --insert-amber: #d9a048;
    --insert-dark: #3a2410;
    --devil-red: #e0222a;
    --sky-blue: #a9d6e6;
    --sky-cream: #f6efd6;
    --stone: #b9b3a6;
    --brand-red: #cf1f2a;
    --ink: #222222;
    --story-ink: #555555;
    --rule: #444444;
    --diagram-fill: #f1f1f1;
  }
  * { margin: 0; padding: 0; box-sizing: border-box; }
  html, body { width: 1098px; height: 1200px; overflow: hidden; }
  body {
    position: relative;
    background: radial-gradient(ellipse at 50% 8%, var(--backdrop-top) 0%, #d6d6d6 45%, var(--backdrop-bottom) 100%);
    font-family: "Arimo", Arial, sans-serif;
  }
  .panel { position: absolute; width: 454px; overflow: hidden; }
  .hang-hole {
    position: absolute; width: 54px; height: 54px; border-radius: 50%;
    background: var(--white); box-shadow: inset 0 1px 3px rgba(0,0,0,.25);
  }

  /* Front panel */
  .front {
    left: 55px; top: 144px; height: 977px;
    background: linear-gradient(180deg, var(--hell-black) 0%, #2b120b 22%, var(--hell-brown) 45%, #6a2a12 60%, #8fb9c9 66%, var(--cloud-blue) 72%, var(--cloud-light) 100%);
  }
  .front .hang-hole { left: 193px; top: 24px; }
  .pair-count {
    position: absolute; left: 300px; top: 52px;
    font-family: "Tenor Sans", sans-serif; font-size: 13px; color: var(--white);
  }
  .devil-shoe-art {
    position: absolute; left: 34px; top: 32px; width: 124px; height: 126px;
    border-radius: 30px 30px 12px 40px;
    background: linear-gradient(150deg, #f0343a 0%, var(--devil-red) 50%, #a8121a 100%);
  }
  .flames-left {
    position: absolute; left: 0; top: 200px; width: 150px; height: 420px;
    border-radius: 0 70px 0 0;
    background: linear-gradient(180deg, rgba(184,48,14,0) 0%, var(--flame-deep) 25%, var(--flame) 60%, var(--flame-light) 100%);
  }
  .flames-right {
    position: absolute; right: 0; top: 380px; width: 70px; height: 240px;
    border-radius: 50px 0 0 0;
    background: linear-gradient(180deg, rgba(184,48,14,0) 0%, var(--flame-deep) 30%, var(--flame) 70%, var(--flame-light) 100%);
  }
  .headline {
    position: absolute; left: 176px; top: 198px;
    font-family: "Cinzel", serif; font-weight: 600; color: var(--gold); line-height: 52px;
  }
  .headline .line { display: block; font-size: 46px; letter-spacing: 1px; }
  .headline .hell { color: var(--white); font-size: 64px; line-height: 76px; }
  .insert-photo {
    position: absolute; left: 32px; top: 410px; width: 398px; height: 274px;
    border-radius: 48% 46% 42% 44% / 52% 50% 46% 48%;
    border: 7px solid var(--white);
    background: radial-gradient(ellipse at 45% 40%, #e6b565 0%, var(--insert-amber) 60%, #b97e30 100%);
  }
  .insert-name {
    position: absolute; left: 108px; top: 588px;
    font-family: "Marcellus", serif; font-size: 50px; line-height: 56px; color: var(--insert-dark);
  }
  .insert-side {
    position: absolute; left: 334px; top: 616px;
    font-family: "Marcellus", serif; font-size: 30px; line-height: 32px; color: var(--insert-dark);
  }
  .shoe-photo {
    position: absolute; left: 252px; top: 712px; width: 152px; height: 176px;
    border-radius: 60px 20px 24px 70px;
    background: linear-gradient(160deg, #f4f8fc 0%, #d3dfea 55%, #aebfcf 100%);
  }
  .tagline {
    position: absolute; left: 17px; top: 740px; width: 250px;
    font-family: "Exo 2", sans-serif; font-style: italic; font-weight: 700;
    font-size: 20px; line-height: 28px; color: var(--tagline-blue);
  }

  /* Back panel */
  .back {
    left: 580px; top: 146px; height: 904px;
    background: linear-gradient(180deg, var(--sky-blue) 0%, #d7ecf0 15%, var(--sky-cream) 35%, #f3ead0 60%, #d9d2bf 80%, var(--stone) 100%);
  }
  .sky-stairs-art {
    position: absolute; left: 0; top: 0; width: 100%; height: 100%;
    background: linear-gradient(180deg, rgba(255,252,235,0) 20%, rgba(255,252,235,.55) 45%, rgba(255,252,235,0) 75%);
  }
  .back .hang-hole { left: 200px; top: 21px; }
  .brand-name {
    position: absolute; left: 0; width: 100%; top: 128px; text-align: center;
    font-family: "Marcellus", serif; font-size: 48px; line-height: 56px; color: var(--brand-red);
  }
  .promise {
    position: absolute; left: 0; width: 100%; top: 236px; text-align: center;
    font-family: "Marcellus", serif; font-size: 28px; line-height: 36px; color: var(--ink);
  }
  .placement-steps {
    position: absolute; left: 27px; top: 342px; width: 400px; height: 110px;
    display: flex; background: var(--white); border: 1px solid var(--rule);
  }
  .step { position: relative; flex: 1; border-right: 1px solid var(--rule); }
  .step:last-child { border-right: 0; }
  .step-number {
    position: absolute; left: 2px; top: 2px; width: 13px; height: 13px;
    background: var(--brand-red); color: var(--white); font-size: 8px; text-align: center; line-height: 13px;
  }
  .step-diagram {
    position: absolute; left: 20px; top: 12px; width: 60px; height: 56px;
    border: 1.5px solid var(--ink); border-radius: 45%; background: var(--diagram-fill);
  }
  .step-diagram.foot { border-radius: 40% 40% 30% 30%; width: 40px; left: 30px; }
  .step-caption {
    position: absolute; left: 3px; right: 3px; top: 80px; text-align: center;
    font-size: 6.5px; line-height: 9px; color: var(--brand-red);
  }
  .story {
    position: absolute; left: 33px; top: 492px; width: 389px; height: 266px;
    border-radius: 24px; background: rgba(255,255,255,.6); text-align: center;
  }
  .story h2 {
    margin-top: 20px; font-family: "Marcellus", serif; font-weight: 400;
    font-size: 30px; line-height: 36px; color: var(--brand-red);
  }
  .story p {
    margin: 4px auto 0; width: 356px; font-style: italic;
    font-size: 10.8px; line-height: 16.4px; color: var(--story-ink);
  }
  .barcode-label {
    position: absolute; left: 314px; top: 764px; width: 120px; height: 78px;
    background: var(--white);
  }
  .site {
    position: absolute; left: 33px; top: 826px;
    font-family: "Marcellus", serif; font-size: 16px; color: var(--ink);
  }
  .origin {
    position: absolute; left: 342px; top: 848px;
    font-family: "Marcellus", serif; font-size: 9px; color: var(--ink);
  }
</style>
</head>
<body>

<section class="panel front">
  <div class="devil-shoe-art" role="img" aria-label="Red devil high-heel illustration with horns and tail"></div>
  <div class="flames-left" role="img" aria-label="Flames rising on the left side"></div>
  <div class="flames-right" role="img" aria-label="Flames on the right side"></div>
  <div class="hang-hole"></div>
  <p class="pair-count">1 Interchangeable Pair</p>
  <h1 class="headline">
    <span class="line">Living in</span>
    <span class="line">High Heel</span>
    <span class="line hell">Hell?</span>
  </h1>
  <div class="insert-photo" role="img" aria-label="Amber gel insert visible through the package"></div>
  <span class="insert-name">Solvara</span>
  <span class="insert-side">R</span>
  <div class="shoe-photo" role="img" aria-label="Pair of white peep-toe high heels"></div>
  <p class="tagline">Then try the only<br>High Heel Insert with a<br>Metatarsal Depression<br>that Relieves Ball of<br>Foot Pain!</p>
</section>

<section class="panel back">
  <div class="sky-stairs-art" role="img" aria-label="Sunlit sky with clouds and a stone stairway"></div>
  <div class="hang-hole"></div>
  <p class="brand-name">Solvara</p>
  <p class="promise">High-Heel Heaven<br>for the Soles of Your Feet!</p>

  <div class="placement-steps">
    <div class="step">
      <span class="step-number">1</span>
      <div class="step-diagram" role="img" aria-label="Insert outline marked left or right"></div>
      <p class="step-caption">L = Left Shoe<br>R = Right Shoe</p>
    </div>
    <div class="step">
      <span class="step-number">2</span>
      <div class="step-diagram" role="img" aria-label="Insert outline with top and bottom stickers"></div>
      <p class="step-caption">Peel top sticker cover<br>&amp; adjust in shoe</p>
    </div>
    <div class="step">
      <span class="step-number">3</span>
      <div class="step-diagram foot" role="img" aria-label="Foot outline with ball of foot marked"></div>
      <p class="step-caption">Depressed area sits<br>under ball of foot</p>
    </div>
    <div class="step">
      <span class="step-number">4</span>
      <div class="step-diagram" role="img" aria-label="Insert outline with bottom sticker lifted"></div>
      <p class="step-caption">Lift bottom slightly<br>&amp; secure sticker</p>
    </div>
  </div>

  <div class="story">
    <h2>Our Story</h2>
    <p>Lorem ipsum dolor sit amet, consectetuer adipiscing elit, sed diam nonummy nibh euismod tincidunt ut laoreet dolore magna aliquam erat volutpat. Ut wisi enim ad minim veniam, quis nostrud exerci tation ullamcorper suscipit lobortis nisl ut aliquip ex ea commodo consequat. Duis autem vel eum iriure dolor in hendrerit in vulputate velit esse molestie consequat, vel illum dolore eu feugiat nulla facilisis at vero eros et accumsan et iusto odio dignissim qui blandit praesent luptatum zzril delenit augue duis dolore te feugait nulla facilisi. Nam liber tempor cum soluta nobis eleifend option congue nihil imperdiet doming id quod mazim placerat facer possim assum. Typi non habent claritatem insitam; est usus legentis in iis qui facit eorum claritatem.</p>
  </div>

  <div class="barcode-label" role="img" aria-label="Retail barcode label area"></div>
  <p class="site">solvara.com</p>
  <p class="origin">Made in China</p>
</section>

</body>
</html>
```